Corporate website design needed

We need a Contemporary Industrial/Tech/Logistics Website design to match our logistic client's business. Our client consults and build logistics solutions that they manage but they are not a typical 3PL (3rd party logistics company) which is primarily engaged in moving boxes.
PSD file only for now, home and default templates.
COMPANY CHARACTER
DESIGN LOOK AND FEEL
• The design should also be modern and visually well organized — employing a combination of visual devices and info graphics. Keep it light and not too heavy but strong/ professional. And unique.
• The design should go beyond the typical industrial pick and pack 3PL representing [Logistics Company] as a High Tech/IT logistics company.
Some examples although these are not right for this client because they have much more content and present themselves more as a 3pl.
http://www.vobrelink-hub.example/ (More right then wrong - Like this but simplified)
http://www.durmaxfreight.example (Ugly)
http://www.tpwallerton.example (More right then wrong but different focus)
http://www.pelhamrye.example/ Too 3PL trucking… We want a bit ore high level approach
The difference, the design should be a fusion in core concepts that culminate in a design which implies the following attributes. Tech (Big data / analytics / software), Consultancy (Solutions, SME, Leader), 3PL Industry vertical solutions.
NOTE: The visualization of “tech” is not “1” and “0”, but more “software and analytics” Perhaps more like www.navimetra.example.
• They need to be seen as a solutions provider in Logistics and as in Subject matter experts
TONE
The tone needs to exude professionalism, expertise, though leadership along with technical and executional excellence.
Experienced
Knowledgeable
Confident
Determined
Straightforward
WEBSITE OBJECTIVES
• Focus C-Suite executives and logistics managers’ attention on [Logistics Company]s commanding knowledge and expertise, and unique approach to supply chain solutions producing more RFP wins
• Create an easy to scan design which decreases the reliance on text through featured text, summaries, and smaller “chunked” size bits of information.
• Convey [Logistics Company] as high-tech 3PL solutions developer and services provider with a ‘high-touch’ consultative approach.
• Showcase [Logistics Company]’s value propositions. (See Slider Content)
• Showcase [Logistics Company]’s expertise in logistical analytics.
• Gain recognition as an industry leader in evolutionary new space (supply chain 2.0)
WEBSITE STRATEGY
• Reduce reliance on text (at least within initial entry points for each section)
• Typography: Watch text line lengths and readability, bolder fonts. NO SERIFS
• Generally, create a click-through format so that users who want more details can find it, and those who don’t can get a snapshot without clicking through.
• Increase visual content through info graphics and some dynamic content, photography
• Better utilize the space on each page (e.g., add visual interest, photography and iconography where appropriate to break up copy blocks and maintain readable line lengths).
COLOR SCHEME
• Create a more engaging color scheme (the logo will remain the same under all circumstances).
• Red / grayscale may work…. Not too dark or heavy. Not too much red. Ex. quiltora.example
• Also try blues and greys. They seem to like that. Open to suggestions but don’t get to crazy. Red is in their logo but too much may be a problem.
PHOTOGRAPHY
Yes. And I will upload some.
If you pick photography please be sure to note Which stock house used and the image number!
CONTENT
The content will be presented in a more hierarchical format — with lead-ins, paragraph and section headers and navigational cues to expand lengthier content allowing the visitor to more easily scan the website. No case studies, No Social media, News while on the home page should not be over emphasized. They don't post a lot so it gets dated quickly ...
I will be uploading a wire frame and other elements.
NOTE: I uploaded my EXAMPLE mock up which is close but not close enough.
I am not a great designer. So I am looking for an alternative that exceed my design ability! These examples show the basic layout but I really want some varied alternatives.
The colors are inconsistent and type not quite right. The grey bar at top is not right and should probably go away.
Please pull the basic elements in the example together into a great design.
If you have questions please contact me.
i will upload some photography tomorrow that may be of use.
Thanks!
Updates
Hi All,
We are still evaluating the submitted designs. Sorry for the delay.
Target Market(s)
This website is primarily a validation website. Few new customers will search and find them as such...
The site should be Focused on C-Suite executives and logistics managers’ attention on [Logistics Company]s commanding knowledge and expertise, and unique approach to supply chain solutions producing more RFP wins
Industry/Entity Type
Business
Font styles to use
Requirements
Must have
- Slide show, Clearly explain who they are and what they do.
Create an easy to scan design which decreases the reliance on text through featured text, summaries, and smaller “chunked” size bits of information.
Convey [Logistics Company] as high-tech 3PL solutions developer and services
provider with a ‘high-touch’ consultative approach.
Should not have
- No Ads space
No Social media
Not too cluttered. Keep it clean.

```html
<!DOCTYPE html>
<html lang="en">
<head>
<meta charset="utf-8">
<title>Northvale Logistics</title>
<link href="https://fonts.googleapis.com/css2?family=Open+Sans:wght@400;600;700&family=Arimo:wght@400;700&display=swap" rel="stylesheet">
<style>
:root{
  --red:#a3123a;
  --red-dark:#8c0f31;
  --ink:#2b2b2b;
  --grey:#8a8a8a;
  --light:#f1f1f1;
  --line:#dcdcdc;
  --footer:#222222;
  --footer-bottom:#2c2c2c;
  --footer-text:#d6d6d6;
}
*{margin:0;padding:0;box-sizing:border-box}
html,body{width:758px;height:1200px;overflow:hidden;background:#fff}
body{position:relative;font-family:'Open Sans',sans-serif;color:var(--ink)}
.abs{position:absolute}
.top-rule{left:0;top:0;width:758px;height:3px;background:var(--red)}
.utility-bar{left:356px;top:0;width:402px;height:27px;background:var(--red);clip-path:polygon(0 0,100% 0,100% 100%,17px 100%);display:flex;justify-content:flex-start;align-items:center;padding-left:23px;gap:6px;color:#fff;font-size:8.2px;white-space:nowrap}
.utility-bar span.sep{opacity:.9}
.brand{left:90px;top:22px;display:flex;align-items:center;gap:7px}
.brand-dot{width:22px;height:22px;border-radius:50%;background:var(--red)}
.brand-name{font-size:13px;font-weight:700;color:var(--ink);letter-spacing:1.5px;line-height:1.15}
.main-nav{top:47px;left:434px;display:flex;align-items:center;font-size:10px;color:#555;white-space:nowrap}
.main-nav a{color:#555;text-decoration:none;margin-right:27px}
.main-nav a.active{color:var(--red)}
.main-nav .divider{margin-right:14px;color:#777}
.header-rule{left:0;top:79px;width:758px;height:1px;background:#e4e4e4}
.hero{left:0;top:80px;width:758px;height:289px;background:linear-gradient(110deg,#1a39c9 0%,#1b6fd6 40%,#1aa6c4 70%,#1cb08a 100%)}
.hero-title{top:190px;left:0;width:758px;text-align:center;color:#fff;font-size:24px;line-height:1.1;font-weight:400}
.hero-title small{display:block;font-size:18.5px;margin-top:3px}
.hero-arrow{top:208px;width:18px;height:18px;border-radius:50%;background:rgba(255,255,255,.35)}
.intro{left:89px;top:387px;width:580px;height:55px;background:var(--light);text-align:center;font-size:11.2px;line-height:16.5px;padding:11px 20px;color:#333}
.pager{top:456px;width:10px;height:10px;border-radius:50%;background:#a9a9a9}
.service-icon{width:58px;height:58px;border-radius:50%;background:#f3f3f3;border:1px solid #e6e6e6;display:flex;align-items:center;justify-content:center}
.service-card{width:201px;height:67px;background:#f4f4f4;border:1px solid #e4e4e4;padding:7px 8px;box-shadow:0 1px 2px rgba(0,0,0,.06)}
.service-card h3{font-size:7.2px;font-weight:600;color:#333;margin-bottom:3px;white-space:nowrap}
.service-card p{font-family:Arimo,sans-serif;font-size:6.6px;line-height:8.4px;color:#444;text-align:justify}
.service-card .more{font-family:Arimo,sans-serif;font-size:6.2px;font-weight:700;color:#333;margin-top:4px}
.service-card::before{content:"";position:absolute;left:-6px;top:29px;border:5px solid transparent;border-right-color:#e4e4e4;border-left:0}
.row-rule{left:89px;top:562px;width:580px;height:1px;background:#e6e6e6}
.section-title{font-size:12px;font-weight:600;color:var(--red)}
.points{left:89px;top:694px;width:325px;list-style:none;font-size:8.3px;line-height:12px;color:#555}
.points li{position:relative;padding-left:10px;margin-bottom:7px}
.points li::before{content:"";position:absolute;left:0;top:4px;width:4px;height:4px;border-radius:50%;background:#333}
.video{left:424px;top:682px;width:112px;height:74px;background:linear-gradient(180deg,#5a5a5a,#b9b9b9 55%,#6f6f6f)}
.play{left:470px;top:709px;width:20px;height:20px;border-radius:50%;background:#222;border:2px solid #fff}
.play::after{content:"";position:absolute;left:6px;top:4px;border:4px solid transparent;border-left:6px solid #fff}
.diff-title{left:546px;top:683px;font-size:12px;line-height:15px;font-weight:600;color:var(--red)}
.diff-text{left:548px;top:716px;width:125px;font-size:7.8px;line-height:11.5px;color:#999}
.news{left:89px;width:325px}
.news h4{font-size:8.5px;font-weight:400;color:#222;margin-bottom:4px}
.news p{font-size:6.8px;line-height:11px;color:#999}
.news .read{font-size:9px;color:#333;margin-top:2px}
.contact-form{left:424px;top:782px;width:244px;height:134px;border:1px solid #e2e2e2;padding-top:10px;text-align:center}
.contact-form h3{font-size:12px;font-weight:600;color:var(--red)}
.field{width:107px;height:18px;border:1px solid #d0d0d0;background:#f8f8f8;font-size:7px;color:#888;padding:4px 5px;text-align:left}
.submit{left:514px;top:881px;width:64px;height:19px;background:var(--red);color:#fff;font-size:8.5px;font-weight:700;display:flex;align-items:center;justify-content:center;border-bottom:2px solid var(--red-dark)}
.footer{left:0;top:935px;width:758px;height:217px;background:var(--footer)}
.footer-col{top:967px;color:var(--footer-text);white-space:nowrap}
.footer-col h5{font-size:11.8px;font-weight:400;color:#fff;margin-bottom:6px}
.footer-col ul{list-style:none;font-family:Arimo,sans-serif;font-size:7.3px;line-height:15.5px}
.footer-col.process ul{line-height:17.7px}
.footer-bottom{left:0;top:1152px;width:758px;height:48px;background:var(--footer-bottom);color:#aaa;font-size:7.4px;padding:17px 0 0 89px}
</style>
</head>
<body>
<div class="abs top-rule"></div>
<nav class="abs utility-bar"><span>Company</span><span class="sep">|</span><span>Careers</span><span class="sep">|</span><span>Contact</span><span class="sep">|</span><span>Search</span><span class="sep">|</span><span>Sales: 866-555-0142</span></nav>

<div class="abs brand"><span class="brand-dot"></span><span class="brand-name">NORTHVALE<br>LOGISTICS</span></div>

<nav class="abs main-nav">
  <a class="active">Solutions</a><a>Our Process</a><a>Industries</a><span class="divider">|</span>
  <svg width="10" height="10" viewBox="0 0 10 10"><circle cx="4" cy="4" r="3" fill="none" stroke="#a3123a" stroke-width="1.4"/><line x1="6.2" y1="6.2" x2="9.2" y2="9.2" stroke="#a3123a" stroke-width="1.5"/></svg>
</nav>
<div class="abs header-rule"></div>

<section class="abs hero" role="img" aria-label="Network of connected data points over a blue-to-green gradient"></section>
<div class="abs hero-arrow" style="left:89px"></div>
<div class="abs hero-arrow" style="left:650px"></div>
<h1 class="abs hero-title">PROVIDING ACTIONABLE STRATEGIES<small>BASED ON DATA-DRIVEN INSIGHTS</small></h1>

<p class="abs intro">Northvale manages complexity, provides data-driven solutions and implements innovation and actionable strategies that delivers business results.</p>
<div class="abs pager" style="left:646px"></div>
<div class="abs pager" style="left:659px"></div>

<div class="abs service-icon" style="left:89px;top:484px"><svg width="28" height="26" viewBox="0 0 28 26"><rect x="1" y="1" width="26" height="18" fill="none" stroke="#a3123a" stroke-width="3"/><rect x="11" y="19" width="6" height="4" fill="#a3123a"/><rect x="6" y="23" width="16" height="3" fill="#a3123a"/></svg></div>
<div class="abs service-card" style="left:165px;top:480px"><h3>MATERIAL MANAGEMENT &amp; FACTORY SUPPORT</h3><p>Lorem ipsum dolor sit amet, consectetur adipisicing elit, sed do eiusmod tempor incididunt ut labore et dolore magna aliqua. Ut enim ad minim veniam</p><div class="more">READ MORE ▸</div></div>

<div class="abs service-icon" style="left:392px;top:484px"><svg width="28" height="26" viewBox="0 0 28 26"><rect x="2" y="5" width="14" height="9" rx="3" fill="#a3123a"/><rect x="10" y="9" width="14" height="12" rx="5" fill="#a3123a"/><circle cx="19" cy="6" r="4" fill="#a3123a"/></svg></div>
<div class="abs service-card" style="left:468px;top:480px"><h3>RETAIL AND E-COMMERCE DISTRIBUTION</h3><p>Lorem ipsum dolor sit amet, consectetur adipisicing elit, sed do eiusmod tempor incididunt ut labore et dolore magna aliqua. Ut enim ad minim veniam</p><div class="more">READ MORE ▸</div></div>

<div class="abs row-rule"></div>

<div class="abs service-icon" style="left:89px;top:579px"><svg width="28" height="28" viewBox="0 0 28 28"><rect x="1" y="16" width="6" height="11" fill="#a3123a"/><rect x="10" y="10" width="6" height="17" fill="#a3123a"/><rect x="19" y="4" width="6" height="23" fill="#a3123a"/><path d="M2 11 L10 5 L14 8" fill="none" stroke="#a3123a" stroke-width="2"/></svg></div>
<div class="abs service-card" style="left:165px;top:575px"><h3>AFTERMARKET SUPPORT</h3><p>Lorem ipsum dolor sit amet, consectetur adipisicing elit, sed do eiusmod tempor incididunt ut labore et dolore magna aliqua. Ut enim ad minim veniam</p><div class="more">READ MORE ▸</div></div>

<div class="abs service-icon" style="left:392px;top:579px"><svg width="20" height="30" viewBox="0 0 20 30"><rect x="1" y="1" width="18" height="28" rx="3" fill="#a3123a"/><rect x="4" y="5" width="12" height="18" fill="#fff"/><circle cx="10" cy="26" r="1.3" fill="#fff"/></svg></div>
<div class="abs service-card" style="left:468px;top:575px"><h3>CRITICAL LOGISTICS</h3><p>Lorem ipsum dolor sit amet, consectetur adipisicing elit, sed do eiusmod tempor incididunt ut labore et dolore magna aliqua. Ut enim ad minim veniam</p><div class="more">READ MORE ▸</div></div>

<h2 class="abs section-title" style="left:89px;top:670px">A DIFFERENT PERSPECTIVE</h2>
<ul class="abs points">
  <li>We commit our own capital and resources to align with our clients' goals</li>
  <li>Unlike consultants, we implement and operate the solutions we design</li>
  <li>We guarantee business performance for our clients by investing in and executing the solutions we design</li>
</ul>
<div class="abs video" role="img" aria-label="Video still of a modern presentation room"></div>
<div class="abs play"></div>
<h2 class="abs diff-title">THE NORTHVALE<br>DIFFERENCE</h2>
<p class="abs diff-text">porta Suspendisse quam leo molestie sed luctus quis feugiat in pede Fusce tellus</p>

<h2 class="abs section-title" style="left:89px;top:777px">RECENT NEWS</h2>
<article class="abs news" style="top:803px"><h4>Northvale Logistics Ranked #1 in Distribution Operations in the Memphis area</h4><p>CARROW POINT, NC — May 10, 2013 – Northvale Logistics, Inc., headquartered in Carrow Point, North Carolina, has once...</p><div class="read">Read More</div></article>
<article class="abs news" style="top:866px"><h4>Northvale Logistics Ranked #1 in Distribution Operations in the Memphis area</h4><p>CARROW POINT, NC — May 10, 2013 – Northvale Logistics, Inc., headquartered in Carrow Point, North Carolina, has once...</p><div class="read">Read More</div></article>

<form class="abs contact-form"><h3>QUICK CONTACT FORM</h3></form>
<div class="abs field" style="left:433px;top:817px">Your Name</div>
<div class="abs field" style="left:552px;top:817px">Phone Number</div>
<div class="abs field" style="left:433px;top:845px">Email</div>
<div class="abs field" style="left:552px;top:845px">Message</div>
<div class="abs submit">SUBMIT</div>

<footer class="abs footer"></footer>
<div class="abs footer-col process" style="left:89px"><h5>Our Process</h5><ul><li>Concept of operations</li><li>Supplying the infrastructure</li><li>Analyzing the data</li><li>Managing complexity</li><li>Providing actionable strategies</li><li>Investing in our client's success</li><li>Driving business results</li></ul></div>
<div class="abs footer-col" style="left:211px"><h5>Our Solutions</h5><ul><li>Business Analytics</li><li>Geographic Coverage</li><li>Project Financing</li><li>Project Implementation</li><li>Technology</li><li>Quality</li></ul></div>
<div class="abs footer-col" style="left:321px"><h5>Industries We Serve</h5><ul><li>Aerospace</li><li>Defense</li><li>Industrial</li><li>Manufacturing</li><li>Media and Entertainment</li><li>Medical</li><li>Retail</li><li>Telecom &amp; Electronics</li></ul></div>
<div class="abs footer-col" style="left:461px"><h5>Company</h5><ul><li>Culture</li><li>Community Involvement</li><li>Major Metro Presence</li><li>News</li><li>Carreers</li><li>Contact</li></ul></div>
<div class="abs footer-col" style="left:563px;top:969px"><h5>Contact Us</h5><ul><li>Northvale Logistics</li><li>2150 Linden Parkway</li><li>Carrow Point, NC 27000</li><li>336-555-0187</li><li>info@northvale.example</li><li>Sales Inquiries: 866-555-0142</li></ul></div>
<div class="abs footer-bottom">© 2014 Company Name &nbsp;All right reserved &nbsp;Term of Use</div>
</body>
</html>
```